Vantoq Business Card Project showing the logo and a marbo image on the rear

Design a whacky but professional business card, the logo is for the front and the Marbo image is for the rear. Happy to consider other open source Marbo Images if the designer wants to select one from the web. Vantoq is a competitor to OMB.com.au and Pellory.com.au and is based around every property in Australia

Target Market(s)

Business

Contact Information for Business Card

Name, Title, Email, Web, Phone Number

Font styles to use
Other font styles liked:
• avenir

Requirements
Must have
• Image on Back logo on front
Nice to have
• Happy to consider other images on rear, preftably Colin Marbo. Image supplied I own, we can use open source other Marbo Images

```html
<!DOCTYPE html>
<html lang="en">
<head>
<meta charset="utf-8">
<title>Vantoq Business Card</title>
<link rel="stylesheet" href="https://fonts.googleapis.com/css2?family=Nunito+Sans:wght@400;700;800&display=swap">
<style>
  :root {
    --page-bg: #e9e4dc;
    --card-bg: #f1f0ee;
    --card-edge: #dcdad6;
    --ink: #1d1d1f;
    --accent: #ee8a1c;
    --accent-dark: #c96f0c;
    --icon-ink: #3a2a14;
    --art-pink: #e6569a;
    --art-yellow: #e9d94a;
    --art-blue: #4fa3d9;
    --art-green: #7cc04b;
  }
  * { box-sizing: border-box; margin: 0; padding: 0; }
  html, body {
    width: 1054px;
    height: 1200px;
    overflow: hidden;
    background: var(--page-bg);
    font-family: "Nunito Sans", "Avenir", sans-serif;
    color: var(--ink);
  }
  .card {
    position: absolute;
    left: 241px;
    top: 172px;
    width: 518px;
    height: 858px;
    background: linear-gradient(180deg, #f6f5f3 0%, var(--card-bg) 60%, #e8e6e2 100%);
    border: 1px solid var(--card-edge);
    border-radius: 16px;
    overflow: hidden;
    text-align: center;
  }
  .brand {
    position: absolute;
    top: 66px;
    left: 0;
    width: 100%;
    height: 100px;
    display: flex;
    justify-content: center;
    align-items: center;
    gap: 18px;
  }
  .brand-mark {
    width: 64px;
    height: 64px;
    background: var(--accent);
    border-radius: 5px;
  }
  .brand-name {
    font-size: 78px;
    font-weight: 800;
    line-height: 1;
    color: var(--ink);
  }
  .person-name {
    position: absolute;
    top: 254px;
    width: 100%;
    font-size: 32px;
    line-height: 40px;
    font-weight: 700;
  }
  .person-title {
    position: absolute;
    top: 301px;
    width: 100%;
    font-size: 21px;
    line-height: 26px;
    font-weight: 400;
    color: var(--accent);
  }
  .contact-divider {
    position: absolute;
    top: 366px;
    left: 0;
    width: 100%;
    height: 40px;
    display: flex;
    justify-content: center;
    align-items: center;
    gap: 18px;
  }
  .divider-line {
    width: 96px;
    height: 2px;
    background: var(--accent);
  }
  .contact-icons { display: flex; gap: 4px; }
  .contact-icons svg { width: 38px; height: 38px; display: block; }
  .contact-list {
    position: absolute;
    top: 417px;
    width: 100%;
    list-style: none;
    font-size: 22px;
    line-height: 32.5px;
  }
  .address {
    position: absolute;
    top: 550px;
    width: 100%;
    font-size: 22px;
    line-height: 30px;
  }
  .rear-artwork {
    position: absolute;
    left: 0;
    bottom: 0;
    width: 100%;
    height: 220px;
    background:
      linear-gradient(180deg, rgba(241,240,238,0) 0%, rgba(241,240,238,0) 75%, rgba(124,192,75,0.9) 100%),
      linear-gradient(90deg, var(--art-pink) 0%, var(--art-yellow) 22%, var(--art-blue) 40%, var(--art-pink) 58%, var(--art-yellow) 78%, var(--art-blue) 100%);
    opacity: 0.85;
  }
</style>
</head>
<body>
  <main class="card">
    <div class="brand">
      <span class="brand-mark"></span>
      <span class="brand-name">Vantoq</span>
    </div>

    <h1 class="person-name">Neil Carrow</h1>
    <p class="person-title">Founder &amp; CEO</p>

    <div class="contact-divider">
      <span class="divider-line"></span>
      <div class="contact-icons">
        <svg viewBox="0 0 48 48" aria-label="Phone">
          <circle cx="24" cy="24" r="22" fill="var(--accent)" stroke="var(--accent-dark)" stroke-width="2"/>
          <path d="M15 20c0-3 3-5 9-5s9 2 9 5l-3 2-2-3h-8l-2 3z" fill="none" stroke="var(--icon-ink)" stroke-width="1.8" stroke-linejoin="round"/>
          <rect x="16" y="24" width="16" height="9" rx="2" fill="none" stroke="var(--icon-ink)" stroke-width="1.8"/>
        </svg>
        <svg viewBox="0 0 48 48" aria-label="Email">
          <circle cx="24" cy="24" r="22" fill="var(--accent)" stroke="var(--accent-dark)" stroke-width="2"/>
          <rect x="13" y="16" width="22" height="16" rx="1.5" fill="none" stroke="var(--icon-ink)" stroke-width="1.8"/>
          <path d="M13 17l11 9 11-9" fill="none" stroke="var(--icon-ink)" stroke-width="1.8" stroke-linejoin="round"/>
        </svg>
        <svg viewBox="0 0 48 48" aria-label="Website">
          <circle cx="24" cy="24" r="22" fill="var(--accent)" stroke="var(--accent-dark)" stroke-width="2"/>
          <circle cx="24" cy="24" r="11" fill="none" stroke="var(--icon-ink)" stroke-width="1.8"/>
          <ellipse cx="24" cy="24" rx="5" ry="11" fill="none" stroke="var(--icon-ink)" stroke-width="1.6"/>
          <path d="M13 24h22M15 18h18M15 30h18" stroke="var(--icon-ink)" stroke-width="1.4"/>
        </svg>
      </div>
      <span class="divider-line"></span>
    </div>

    <ul class="contact-list">
      <li class="contact-phone">(00) 4816 2790</li>
      <li class="contact-email">carrow@vantoq.com</li>
      <li class="contact-web">www.vantoq.com</li>
    </ul>

    <p class="address">Level 4, 18 Harlow Lane, Sydney 2000, AU</p>

    <div class="rear-artwork" role="img" aria-label="Multicoloured illustration panel along the base of the card"></div>
  </main>
</body>
</html>
```